Website re-design for Brightmoor LLC website ( has existing website )

Looking to do a complete re-design of Brightmoorllc. The existing website is dated and built in wordpress. The new website will not be wordpress. The project folder includes an overview.txt file with details on the project. The file also contains a list of websites that he/she likes which I am sure is very helpful .
Number of Pages Required
1 page

```html
<!DOCTYPE html>
<html lang="en">
<head>
<meta charset="utf-8">
<title>Brightmoor LLC – Lake Weed Removal</title>
<link href="https://fonts.googleapis.com/css2?family=Fira+Sans:wght@500;600;700&family=Montserrat:wght@400;500;600&display=swap" rel="stylesheet">
<style>
:root{
  --blue:#1459ad;
  --blue-dark:#0f4f9c;
  --ice:#deebf4;
  --ink:#333;
  --muted:#555;
  --white:#fff;
  --black:#0b0b0b;
}
*{box-sizing:border-box;margin:0;padding:0}
html,body{width:1200px;height:5055px;overflow:hidden;background:var(--white)}
body{position:relative;font-family:'Montserrat',sans-serif;color:var(--ink)}
.abs{position:absolute}
h1,h2,h3{font-family:'Fira Sans',sans-serif;color:var(--blue);font-weight:600}
.center{left:0;width:1200px;text-align:center}

/* header */
.topbar{left:451px;top:0;width:510px;height:36px;background:var(--blue);border-radius:0 0 26px 26px;display:flex;align-items:center;justify-content:center;gap:40px;color:var(--white);font-size:11px}
.topbar span{display:flex;align-items:center;gap:8px}
.ico{width:20px;height:20px;border-radius:50%;background:#0c3f7e;display:inline-flex;align-items:center;justify-content:center}
.brand{left:112px;top:14px;display:flex;align-items:center;gap:10px}
.brand-dot{width:62px;height:62px;border-radius:50%;border:4px solid var(--blue);background:var(--white)}
.brand-name{font-family:'Montserrat',sans-serif;font-weight:500;color:var(--blue);font-size:30px}
.nav{right:104px;top:58px;display:flex;gap:36px;font-size:13px;color:var(--ink)}
.nav .active{color:var(--blue);border-bottom:2px solid var(--blue);padding-bottom:6px}

/* hero */
.hero{left:0;top:92px;width:1200px;height:660px;background:linear-gradient(180deg,#5c93d4 0%,#9cc2ea 30%,#3f6f9a 52%,#6f8a5a 70%,#8a6a4e 100%)}
.hero-box{left:261px;top:171px;width:679px;height:153px;background:rgba(110,120,130,.62);text-align:center;color:var(--white)}
.hero-box h1{color:var(--white);font-family:'Fira Sans',sans-serif;font-weight:600;font-size:52px;letter-spacing:2px;margin-top:22px;text-shadow:0 2px 4px rgba(0,0,0,.3)}
.hero-box p{font-size:20px;margin-top:4px}
.btn{left:508px;top:318px;width:169px;height:45px;background:var(--blue);border-radius:23px;color:var(--white);font-size:12px;font-weight:600;display:flex;align-items:center;padding-left:20px;gap:26px}
.btn i{width:34px;height:34px;border-radius:50%;background:var(--white);display:flex;align-items:center;justify-content:center}
.hero-arrow{top:390px;width:44px;height:44px;border:1px solid rgba(255,255,255,.6);border-radius:50%}
.hero-cut{left:0;top:712px;width:1200px;height:40px}

/* dividers */
.divider{display:flex;align-items:center;justify-content:center;gap:10px}
.divider b{display:block;height:2px;background:var(--blue)}
.divider em{width:22px;height:22px;border-radius:50%;background:var(--blue);display:block}
.divider.wide b{width:130px}
.divider.short b{width:66px}
.divider.tiny b{width:42px}
.divider.tiny em{width:20px;height:20px}
.divider.left{justify-content:flex-start}
.sec-title{font-size:34px}
.body-text{font-size:15.5px;line-height:30px;color:var(--muted)}
.justify{text-align:justify}

.photo{border-radius:50%;border:1.5px solid var(--blue);padding:12px;background:var(--white)}
.photo div{width:100%;height:100%;border-radius:50%}

/* services */
.services{left:0;top:2927px;width:1200px;height:616px;background:var(--blue-dark)}
.card{top:3184px;width:226px;height:222px;background:var(--white);display:flex;align-items:center;justify-content:center}
.card div{width:110px;height:110px;border-radius:14px;background:#e6e9ee}
.card-label{top:3423px;width:226px;text-align:center;color:var(--white);font-family:'Fira Sans',sans-serif;font-weight:600;font-size:17px;line-height:21px}

.ba{left:0;top:3543px;width:1200px;height:542px;background:var(--ice)}
.shot{top:3731px;height:266px}
.arrow-btn{top:3840px;width:56px;height:56px;border-radius:50%;background:var(--blue);display:flex;align-items:center;justify-content:center}

/* faq */
.faq{left:261px;width:679px;height:44px;border:1.5px solid var(--blue);border-radius:22px;display:flex;align-items:center;gap:26px;padding-left:12px;font-size:12px;color:var(--ink);background:rgba(255,255,255,.9)}
.faq i{width:24px;height:24px;border-radius:50%;background:var(--blue);color:var(--white);font-style:normal;display:flex;align-items:center;justify-content:center;font-size:14px}
.faq.open{background:var(--blue);color:var(--white)}
.faq.open i{background:var(--white);color:var(--blue)}
.faq-answer{left:322px;top:4440px;width:566px;font-size:12.5px;line-height:23px;color:var(--muted)}

.mist{left:0;top:4560px;width:1200px;height:320px;background:linear-gradient(180deg,#fff 0%,#dfe8ef 45%,#8a9fb2 80%,#2c3b48 100%)}
.footer{left:0;top:4862px;width:1200px;height:193px;background:var(--black)}
.footer-nav{top:4942px;display:flex;justify-content:center;gap:38px;color:var(--white);font-size:13px}
.footer-line{left:112px;top:4989px;width:976px;height:1px;background:#666}
.copy{top:5020px;color:var(--white);font-size:12px}
.totop{left:1120px;top:4965px;width:48px;height:48px;border-radius:50%;background:var(--blue);display:flex;align-items:center;justify-content:center}
</style>
</head>
<body>

<header>
  <div class="abs topbar">
    <span><i class="ico"><svg width="10" height="12" viewBox="0 0 10 12"><path d="M5 0a4 4 0 0 0-4 4c0 3 4 8 4 8s4-5 4-8a4 4 0 0 0-4-4zm0 5.5A1.5 1.5 0 1 1 5 2.5a1.5 1.5 0 0 1 0 3z" fill="#fff"/></svg></i>4187 Birch Hollow Rd, Ridgefield, MN 55402</span>
    <span>|</span>
    <span><i class="ico"><svg width="11" height="11" viewBox="0 0 24 24"><path d="M6.6 10.8a15 15 0 0 0 6.6 6.6l2.2-2.2c.3-.3.7-.4 1-.2 1.1.4 2.3.6 3.6.6.6 0 1 .4 1 1V20c0 .6-.4 1-1 1C10.6 21 3 13.4 3 4c0-.6.4-1 1-1h3.5c.6 0 1 .4 1 1 0 1.3.2 2.5.6 3.6.1.3 0 .7-.2 1z" fill="#fff"/></svg></i>(612) 555-0148</span>
  </div>
  <div class="abs brand"><span class="brand-dot"></span><span class="brand-name">Brightmoor</span></div>
  <nav class="abs nav"><span class="active">Home</span><span>Services</span><span>About Us</span><span>Contact Us</span><span>FAQs</span></nav>
</header>

<section>
  <div class="abs hero" role="img" aria-label="Photo of yellow lawn chairs on a wooden dock beside a calm blue lake with a red flower pot"></div>
  <div class="abs hero-arrow" style="left:32px"></div>
  <div class="abs hero-arrow" style="left:1124px"></div>
  <div class="abs hero-box"><h1>LAKE WEED REMOVAL</h1><p>Specializing In Residential &amp; Commercial</p></div>
  <div class="abs btn">LEARN MORE <i><svg width="14" height="12" viewBox="0 0 14 12"><path d="M1 6h11M7 1l5 5-5 5" stroke="#1459ad" stroke-width="2" fill="none"/></svg></i></div>
  <svg class="abs hero-cut" viewBox="0 0 1200 40" preserveAspectRatio="none"><path d="M0 40 L0 28 L170 28 L190 0 L1010 0 L1030 28 L1200 28 L1200 40Z" fill="#fff"/></svg>
</section>

<section>
  <h2 class="abs center sec-title" style="top:848px">Aquatic Innovators, at Your Service.</h2>
  <div class="abs center divider wide" style="top:903px"><b></b><em></em><b></b></div>
  <p class="abs body-text" style="left:145px;top:935px;width:910px;text-align:center">Brightmoor LLC is a company formed in response to the increasing incidence of invasive species in Minnesota's lakes and water systems. The impact of these fast-growing nuisances, inspired our venture to effectively control unwanted lake weeds. Brightmoor, LLC helps provide the enjoyable weed-free lake environment craved by water enthusiasts.</p>
  <div class="abs" style="left:112px;top:1137px;width:976px;height:1px;background:#bcd2e6"></div>
  <div class="abs" style="left:575px;top:1112px;width:50px;height:50px;border-radius:50%;background:var(--white);border:3px solid #cfe0ef;display:flex;align-items:center;justify-content:center"><span style="width:34px;height:34px;border-radius:50%;background:var(--blue)"></span></div>
</section>

<section>
  <h2 class="abs center sec-title" style="top:1218px">About Us</h2>
  <div class="abs center divider short" style="top:1272px"><b></b><em></em><b></b></div>

  <h3 class="abs" style="left:173px;top:1398px;font-size:28px">Our Mission</h3>
  <div class="abs divider tiny left" style="left:173px;top:1435px"><b></b><em></em><b></b></div>
  <p class="abs body-text justify" style="left:175px;top:1456px;width:430px">Brightmoor LLC is a company formed in response to the increase in invasive species in Minnesota lakes and waterways. The impact of these fast-growing nuisances inspired our venture to effectively control unwanted lake weeds and create an enjoyable environment craved by waterfront property homeowners.</p>
  <div class="abs photo" style="left:689px;top:1352px;width:376px;height:376px"><div role="img" aria-label="Photo of a diver beside a dock covered in removed lake weeds" style="background:linear-gradient(160deg,#7b8f98,#4a5e52 60%,#2e3a33)"></div></div>

  <svg class="abs" style="left:0;top:1805px" width="1200" height="520" viewBox="0 0 1200 520" preserveAspectRatio="none"><path d="M0 60 Q600 -60 1200 60 L1200 520 L0 520Z" fill="#deebf4"/></svg>
  <div class="abs photo" style="left:177px;top:1876px;width:376px;height:376px"><div role="img" aria-label="Photo of a sanded lakeside beach with a blue chair and kayaks" style="background:linear-gradient(180deg,#9fc0d8 0%,#c8b58e 45%,#5c8a3a 100%)"></div></div>
  <h3 class="abs" style="left:653px;top:1922px;font-size:28px">Preserving the Good</h3>
  <div class="abs divider tiny left" style="left:653px;top:1960px"><b></b><em></em><b></b></div>
  <p class="abs body-text justify" style="left:653px;top:1982px;width:430px">We have partnered with The Compost Yard to recycle 100% of the lake weeds we remove. The types of materials used in compost have a huge impact on how long it takes to break down and how nutrient rich the end product will be. The lake weeds we provide have high levels of moisture as well as critically needed nitrogen. They are a great addition for making high quality compost.</p>

  <h3 class="abs" style="left:139px;top:2450px;font-size:28px">Keep Invaders Out of Our Lakes!</h3>
  <div class="abs divider tiny left" style="left:139px;top:2488px"><b></b><em></em><b></b></div>
  <p class="abs body-text justify" style="left:139px;top:2512px;width:500px">Aquatic Invasive species (AIS) are a serious risk to lakes, rivers, streams, and other bodies of water. In many nutrient rich lakes, invasive vegetation can thrive and form dense patches and mats of weeds hazardous to water recreation. Worse than an inconvenience to recreation, invasive species also crowd native plants and cause devastating and lasting effects on the natural ecosystem. We have seen first-hand what these invasive species can do to bodies of water, and want to help you learn about this massive problem in Minnesota. To learn more about invasive species and how they are spread, please visit the Northwoods Waters Agency website.</p>
  <div class="abs photo" style="left:698px;top:2461px;width:376px;height:376px"><div role="img" aria-label="Photo of divers in a lake covered with lily pads" style="background:linear-gradient(180deg,#5f8a3d,#3d6a2e 60%,#2c4a26)"></div></div>
</section>

<section>
  <div class="abs services"></div>
  <h2 class="abs center sec-title" style="top:2998px;color:var(--white)">Services</h2>
  <div class="abs center divider wide" style="top:3050px"><b style="background:#fff"></b><em style="background:#fff"></em><b style="background:#fff"></b></div>
  <p class="abs center" style="top:3090px;color:var(--white);font-size:16px;line-height:31px;font-weight:500">We know there is no life like the lake life and we are dedicated to<br>keeping it that way.</p>
  <div class="abs card" style="left:112px"><div role="img" aria-label="Icon of lake reeds"></div></div>
  <div class="abs card" style="left:363px"><div role="img" aria-label="Icon of a zebra mussel shell"></div></div>
  <div class="abs card" style="left:612px"><div role="img" aria-label="Icon of sparkles"></div></div>
  <div class="abs card" style="left:861px"><div role="img" aria-label="Icon of a beach bucket and shovel"></div></div>
  <p class="abs card-label" style="left:112px">Lake Weed<br>Removal (Submerged)</p>
  <p class="abs card-label" style="left:363px">Zebra Mussel<br>Removal</p>
  <p class="abs card-label" style="left:612px">Shoreline<br>Cleanups</p>
  <p class="abs card-label" style="left:861px">Beach<br>Sanding</p>
</section>

<section>
  <div class="abs ba"></div>
  <h2 class="abs center sec-title" style="top:3614px">Before and After</h2>
  <div class="abs center divider wide" style="top:3668px"><b></b><em></em><b></b></div>
  <div class="abs shot" style="left:0;width:82px;background:linear-gradient(180deg,#a9b8c4,#7c8a80)" role="img" aria-label="Photo of a shoreline after cleanup"></div>
  <div class="abs shot" style="left:129px;width:467px;background:linear-gradient(180deg,#6f8a4a,#5a6a4a 50%,#8a7a62)" role="img" aria-label="Photo of a weed-covered dock before removal"></div>
  <div class="abs shot" style="left:604px;width:467px;background:linear-gradient(180deg,#7e9a52,#6a7a5a 50%,#a99a80)" role="img" aria-label="Photo of the same dock clear of weeds after removal"></div>
  <div class="abs shot" style="left:1118px;width:82px;background:linear-gradient(180deg,#8fa6bd,#5b6f80)" role="img" aria-label="Photo of a lake shoreline"></div>
  <div class="abs arrow-btn" style="left:25px"><svg width="20" height="16" viewBox="0 0 20 16"><path d="M19 8H3M9 2 3 8l6 6" stroke="#fff" stroke-width="2" fill="none"/></svg></div>
  <div class="abs arrow-btn" style="left:1118px"><svg width="20" height="16" viewBox="0 0 20 16"><path d="M1 8h16M11 2l6 6-6 6" stroke="#fff" stroke-width="2" fill="none"/></svg></div>
</section>

<section>
  <div class="abs mist" role="img" aria-label="Misty mountain and forest landscape"></div>
  <h2 class="abs center sec-title" style="top:4156px">Faq's</h2>
  <div class="abs center divider short" style="top:4211px"><b></b><em></em><b></b></div>
  <div class="abs faq" style="top:4263px"><i>+</i>How early do lake weeds start to grow?</div>
  <div class="abs faq" style="top:4325px"><i>+</i>How fast do lake weeds grow?</div>
  <div class="abs faq open" style="top:4386px"><i>-</i>How big of an area can I treat?</div>
  <p class="abs faq-answer">Aquatic plants are extremely important to the ecosystem of each waterway. Because of this, the State Waters Office limits the amount of vegetation homeowners can remove in front of their property (up to 2,500 square feet without a permit, up to 5,000 square feet with a permit). Other limitations may apply dependent on how many feet of shoreline the property has and what type of lake weed proposed to be removed. More information can be found here.</p>
  <div class="abs faq" style="top:4593px"><i>+</i>What if the treatment area encroaches your neighbor's shoreline?</div>
  <div class="abs faq" style="top:4655px"><i>+</i>How long does each treatment last?</div>
  <div class="abs faq" style="top:4716px"><i>+</i>I DO NOT have a natural beach. Can I install one?</div>
</section>

<footer>
  <svg class="abs" style="left:0;top:4830px" width="1200" height="40" viewBox="0 0 1200 40"><path d="M0 40 L140 40 L160 4 L1040 4 L1060 40 L1200 40Z" fill="#0b0b0b"/></svg>
  <div class="abs footer"></div>
  <nav class="abs center footer-nav"><span>Home</span><span>Services</span><span>About Us</span><span>Contact Us</span><span>Blog</span><span>Employment</span><span>FAQs</span></nav>
  <div class="abs footer-line"></div>
  <p class="abs center copy">© 2022 Brightmoor, LLC</p>
  <div class="abs totop"><svg width="14" height="10" viewBox="0 0 14 10"><path d="M1 9l6-7 6 7" stroke="#fff" stroke-width="2" fill="none"/></svg></div>
</footer>

</body>
</html>
```